Online homewares store needs a web design

We need a web design for a new high-end online homewares store. We are starting small with only 5 major categories.

Rugs
Bathe
Dine
Decorative
Sleep

This is just for design. No coding needed.

Please make high-end, sophisticated and minimal.

I have included some pictures to give you an idea of the products. I would like to showcase some of the pictures on the web page.

The website will be using an e-commerce function.

I have included the logo studio nine harbors.

I like this website
http://mapleandquarrylane.example/

or

borvanest.example.au

Simple but effective - not too busy

Project Deadline Extended
Reason: I would like to extend my deadline to give designers more time to do quality work - as requested!! Thanks.

Target Market(s)

Females in the age bracket of 25-45

Males who are very house proud 25-45

Industry/Entity Type

Store

Requirements
Must have
• Upmarket

```html
<!DOCTYPE html>
<html lang="en">
<head>
<meta charset="utf-8">
<title>studio nine harbors — homewares</title>
<link href="https://fonts.googleapis.com/css2?family=Oxygen:wght@300;400;700&display=swap" rel="stylesheet">
<style>
:root{
  --pink:#e5139b;
  --black:#050505;
  --ink:#333;
  --muted:#8a8a8a;
  --paper:#e6e7e9;
  --white:#fff;
  --card-dark:#2f2f2f;
  --rule:#cfcfcf;
}
*{box-sizing:border-box;margin:0;padding:0}
html,body{width:683px;height:1200px;overflow:hidden}
body{position:relative;background:var(--paper);font-family:'Oxygen',Arial,sans-serif;color:var(--ink)}
.abs{position:absolute}
a{color:inherit;text-decoration:none}

/* top bar */
.topbar{left:0;top:0;width:683px;height:36px;background:var(--black)}
.brand{left:44px;top:5px;font-size:22px;font-weight:300;color:var(--white);letter-spacing:-.3px}
.brand-dot{color:var(--pink)}
.account-links{top:12px;font-size:8px;color:#ccc;display:flex;align-items:center;gap:4px}
.account-links i{display:inline-block;width:9px;height:9px;border-radius:50%;background:var(--pink)}
.login{left:522px;top:10px;width:86px;height:15px;background:#3a3a3a;border-radius:2px;font-size:7.5px;color:#fff;text-align:center;line-height:15px}
.login span{color:#999}
.search{left:615px;top:6px;width:22px;height:22px;border-radius:50%;background:var(--pink)}

/* nav */
.nav{left:0;top:36px;width:683px;height:28px;background:var(--white);border-bottom:1px solid #ddd}
.nav-item{top:45px;font-size:8.5px;color:#555}
.nav-sep{top:44px;width:1px;height:12px;background:#ddd}
.home-tab{left:62px;top:36px}
.cart{left:549px;top:42px;width:88px;height:17px;border:1px solid #ddd;background:#f7f7f7;font-size:7.5px;line-height:15px;padding-left:20px;color:#666}
.cart b{color:var(--pink);font-weight:400}

/* hero */
.hero{left:0;top:64px;width:683px;height:354px;background:#e9eaec}
.hero-rug{left:100px;top:92px;width:240px;height:232px;border-radius:50%;background:radial-gradient(circle,#c6a06b 0%,#a98451 55%,#b8925e 75%,#8f6d3e 100%)}
.hero-arrow{width:27px;height:27px;border-radius:50%;background:#fff;border:2px solid #222}
.hero-title{left:355px;top:156px;font-size:21px;font-weight:700;line-height:22px;color:#333}
.hero-copy{left:355px;top:208px;width:210px;font-size:10px;line-height:15px;color:#777}
.purchase{left:357px;top:266px;width:107px;height:25px;background:var(--pink);color:#fff;font-size:13px;font-weight:700;text-align:center;line-height:25px;border-radius:2px}
.price-badge{left:521px;top:120px;width:63px;height:63px;border-radius:50%;background:#fff;border:5px solid var(--pink);text-align:center}
.price-badge s{display:block;font-size:9px;color:#aaa;margin-top:5px}
.price-badge b{display:block;font-size:20px;line-height:18px;color:#111}
.price-badge sup{font-size:9px}
.price-badge em{display:block;font-style:normal;font-size:6.5px;color:var(--pink)}
.tab-rule{left:64px;top:346px;width:556px;height:4px;background:var(--black)}
.tab-rule-active{left:176px;top:346px;width:109px;height:4px;background:var(--pink)}
.cat-tabs{left:64px;top:358px;width:556px;display:flex}
.cat-tab{flex:1;text-align:center;border-right:1px solid #d8d8d8;height:28px}
.cat-tab:last-child{border-right:0}
.cat-tab h3{font-size:10.5px;font-weight:400;color:#777}
.cat-tab p{font-size:7.5px;color:#999;margin-top:2px}
.cat-tab.active h3{color:var(--pink)}
.cat-tab.active p{color:#333}

/* featured */
.featured{left:0;top:418px;width:683px;height:188px;background:var(--black)}
.section-title{font-size:13px;font-weight:400}
.wave{height:6px}
.pager{width:18px;height:18px;border-radius:50%;background:#444}
.f-card{top:467px;width:130px;height:119px;background:#fff;border-radius:3px}
.f-img{position:absolute;left:3px;top:3px;width:124px;height:81px}
.f-name{position:absolute;left:6px;top:90px;font-size:8.5px;color:#333}
.f-no{position:absolute;left:6px;top:104px;font-size:7px;color:#999}
.price{position:absolute;width:41px;height:41px;border-radius:50%;border:3px solid #fff;box-shadow:0 0 0 1px #bbb;background:#2d2d2d;color:#fff;font-size:8.5px;text-align:center;display:flex;flex-direction:column;justify-content:center}
.price.hot{background:var(--pink)}
.price s{font-size:6.5px;color:#ccc}
.hot-flag{position:absolute;right:0;top:0}

/* latest */
.l-card{width:122px;height:114px;background:var(--card-dark);border-radius:2px;border:1px solid #222}
.l-img{position:absolute;left:3px;top:3px;width:114px;height:80px}
.l-name{position:absolute;left:5px;top:86px;font-size:8px;color:#fff}
.l-no{position:absolute;left:5px;top:98px;font-size:7px;color:#ccc}
.l-card .price{background:#fff;color:#222;border-color:#2f2f2f;box-shadow:0 0 0 1px #fff;right:8px;bottom:6px}
.l-card .price.hot{background:var(--pink);color:#fff}
.offer{left:490px;top:650px;width:148px;height:114px;background:#fff;border:1px solid #bbb}
.offer-img{position:absolute;left:2px;top:2px;width:142px;height:70px;background:linear-gradient(135deg,#b44 0%,#dcb 40%,#3a6 60%,#c73 100%)}
.offer-txt{position:absolute;left:6px;top:73px;font-size:13px;line-height:13px;color:#222}
.offer-big{font-size:20px;font-weight:700;color:var(--pink);line-height:22px}
.offer-big span{color:#222}
.offer-big small{font-size:10px;color:var(--pink);font-weight:400}
.womens{left:490px;top:782px;width:148px;height:114px;background:linear-gradient(#5a5a5a,#3c3c3c);border:1px solid #222}
.womens h4{position:absolute;left:10px;top:10px;font-size:12px;color:#fff;line-height:13px;font-weight:700}
.womens p{position:absolute;left:10px;top:38px;width:58px;font-size:6.5px;color:#ddd;line-height:8px}
.buy{position:absolute;left:10px;top:78px;width:26px;height:12px;background:#f5b400;font-size:6px;color:#333;text-align:center;line-height:12px}
.womens-photo{position:absolute;right:0;top:0;width:72px;height:112px;background:linear-gradient(#6a6a6a,#e86a8a 70%,#d45577)}

/* why shop */
.why{left:45px;top:917px;width:593px;height:40px;border-top:1px solid var(--pink);border-bottom:1px solid var(--pink)}
.why-label{left:45px;top:919px;width:107px;height:36px;background:var(--black);color:#fff;font-size:9px;line-height:36px;text-align:center}
.why-item{top:927px;font-size:7.5px;line-height:9px;color:#333;display:flex;gap:5px;align-items:center}

/* follow */
.connect{left:45px;top:976px;width:593px;height:65px;background:var(--black)}
.connect-inner{left:52px;top:983px;width:579px;height:51px;background:#fff}
.connect-label{font-size:8px;color:#333}
.social{display:flex;gap:3px}
.social i{display:block;width:13px;height:13px}
.phone{left:215px;top:1006px;font-size:14px;color:var(--pink)}
.news-input{left:355px;top:1009px;width:219px;height:17px;border:1px solid #ccc;font-size:6.5px;font-style:italic;color:#999;line-height:15px;padding-left:6px}
.submit{left:574px;top:1009px;width:46px;height:17px;background:var(--pink);color:#fff;font-size:9px;font-weight:700;text-align:center;line-height:17px}
.vrule{width:1px;height:51px;top:983px;background:#ddd}

/* footer */
.footer{left:45px;top:1062px;width:593px;height:121px;background:#fff;border:2px solid var(--black)}
.foot-col{top:1078px}
.foot-col h5{font-size:9px;font-weight:400;color:#222;border-left:2px solid var(--pink);padding-left:5px;margin-bottom:4px}
.foot-col ul{list-style:none;display:grid;column-gap:14px;font-size:7px;line-height:14px;color:#444;padding-left:7px}
.foot-brand{left:488px;top:1092px;width:146px;height:24px;background:var(--black);color:#fff;font-size:15px;font-weight:300;text-align:center;line-height:24px}
.accept{left:489px;top:1129px;font-size:7px;font-style:italic;font-weight:700;color:#333}
.pay{top:1129px;width:22px;height:14px;border:1px solid #ccc;border-radius:2px;background:#eee}
.copyright{left:47px;top:1160px;width:589px;border-top:1px solid #ccc;text-align:center;font-size:8px;line-height:20px;color:#222}
</style>
</head>
<body>

<!-- Top bar -->
<header class="abs topbar"></header>
<div class="abs brand">studio nine harbors</div>
<div class="abs account-links" style="left:330px"><i></i>My Account</div>
<div class="abs account-links" style="left:393px"><i></i>Shopping Cart</div>
<div class="abs account-links" style="left:468px"><i></i>Checkout</div>
<div class="abs login">Login <span>-- or --</span> Register</div>
<div class="abs search">
  <svg width="22" height="22" viewBox="0 0 22 22"><circle cx="10" cy="10" r="4" fill="none" stroke="#fff" stroke-width="1.8"/><line x1="13" y1="13" x2="16" y2="16" stroke="#fff" stroke-width="2"/></svg>
</div>

<!-- Navigation -->
<nav class="abs nav"></nav>
<svg class="abs home-tab" width="42" height="38" viewBox="0 0 42 38"><path d="M0 0H42V32L21 38L0 32Z" fill="#e5139b"/><text x="21" y="17" text-anchor="middle" font-family="Oxygen,sans-serif" font-size="8.5" font-weight="700" fill="#fff">Home</text></svg>
<a class="abs nav-item" style="left:112px">Rugs</a>
<div class="abs nav-sep" style="left:145px"></div>
<a class="abs nav-item" style="left:160px">Bathe</a>
<div class="abs nav-sep" style="left:197px"></div>
<a class="abs nav-item" style="left:212px">Dine</a>
<div class="abs nav-sep" style="left:243px"></div>
<a class="abs nav-item" style="left:259px">Decorative</a>
<div class="abs nav-sep" style="left:314px"></div>
<a class="abs nav-item" style="left:330px">Sleep</a>
<div class="abs nav-sep" style="left:366px"></div>
<a class="abs nav-item" style="left:381px">Contact Us</a>
<div class="abs cart">Cart <b>$0.00</b>
  <svg class="abs" style="left:5px;top:3px" width="12" height="10" viewBox="0 0 12 10"><path d="M0 1H2L4 7H10L11 3H3" fill="none" stroke="#e5139b" stroke-width="1.2"/><circle cx="5" cy="9" r="1" fill="#e5139b"/><circle cx="9" cy="9" r="1" fill="#e5139b"/></svg>
  <svg class="abs" style="left:76px;top:6px" width="5" height="4"><path d="M0 0H5L2.5 3Z" fill="#777"/></svg>
</div>

<!-- Hero -->
<section class="abs hero"></section>
<div class="abs hero-rug" role="img" aria-label="Round braided jute rug with scalloped petal edge"></div>
<div class="abs hero-arrow" style="left:64px;top:192px"><svg width="23" height="23" viewBox="0 0 23 23"><path d="M13 7L9 11.5L13 16" fill="none" stroke="#222" stroke-width="2"/></svg></div>
<div class="abs hero-arrow" style="left:592px;top:192px"><svg width="23" height="23" viewBox="0 0 23 23"><path d="M10 7L14 11.5L10 16" fill="none" stroke="#222" stroke-width="2"/></svg></div>
<h1 class="abs hero-title">Decorative<br>Be your best deal</h1>
<p class="abs hero-copy">Nunc non fermentum nunc. Sed ut ante eget leo tempor consequat sit amet eu orci. Donec dignissim dolor eget..</p>
<a class="abs purchase">Purchase</a>
<div class="abs price-badge"><s>$199</s><b><sup>$</sup>130</b><em>Best deal</em></div>

<div class="abs tab-rule"></div>
<div class="abs tab-rule-active"></div>
<div class="abs cat-tabs">
  <div class="cat-tab"><h3>Rugs</h3><p>Lorem Ipsum Sit Dolor</p></div>
  <div class="cat-tab active"><h3>Bathe</h3><p>Lorem Ipsum Sit Dolor</p></div>
  <div class="cat-tab"><h3>Dine</h3><p>Lorem Ipsum Sit Dolor</p></div>
  <div class="cat-tab"><h3>Decorative</h3><p>Lorem Ipsum Sit Dolor</p></div>
  <div class="cat-tab"><h3>Sleep</h3><p>Lorem Ipsum Sit Dolor</p></div>
</div>

<!-- Featured -->
<section class="abs featured"></section>
<h2 class="abs section-title" style="left:44px;top:434px;color:#fff">Featured Products</h2>
<svg class="abs wave" style="left:170px;top:439px" width="415" height="6"><path d="M0 3 q2 -3 4 0 t4 0 t4 0 t4 0 t4 0 t4 0 t4 0 t4 0 t4 0 t4 0 t4 0 t4 0 t4 0 t4 0 t4 0 t4 0 t4 0 t4 0 t4 0 t4 0 t4 0 t4 0 t4 0 t4 0 t4 0 t4 0 t4 0 t4 0 t4 0 t4 0 t4 0 t4 0 t4 0 t4 0 t4 0 t4 0 t4 0 t4 0 t4 0 t4 0 t4 0 t4 0 t4 0 t4 0 t4 0 t4 0 t4 0 t4 0 t4 0 t4 0 t4 0 t4 0 t4 0 t4 0 t4 0 t4 0 t4 0 t4 0 t4 0 t4 0 t4 0 t4 0 t4 0 t4 0 t4 0 t4 0 t4 0 t4 0 t4 0 t4 0 t4 0 t4 0 t4 0 t4 0 t4 0 t4 0 t4 0 t4 0 t4 0 t4 0 t4 0 t4 0 t4 0 t4 0 t4 0 t4 0 t4 0 t4 0 t4 0 t4 0 t4 0 t4 0 t4 0 t4 0 t4 0 t4 0 t4 0 t4 0 t4 0 t4 0" fill="none" stroke="#777" stroke-width=".8"/></svg>
<div class="abs pager" style="left:594px;top:433px"><svg width="18" height="18"><path d="M10 5L6 9L10 13" fill="none" stroke="#ccc" stroke-width="1.2"/></svg></div>
<div class="abs pager" style="left:619px;top:433px"><svg width="18" height="18"><path d="M8 5L12 9L8 13" fill="none" stroke="#ccc" stroke-width="1.2"/></svg></div>

<article class="abs f-card" style="left:45px">
  <div class="f-img" role="img" aria-label="Living room with patterned cream rug and sofa" style="background:linear-gradient(#b09a80,#d8d0c4)"></div>
  <svg class="hot-flag" width="34" height="34"><path d="M4 0H34V30Z" fill="#e5139b"/><text x="24" y="12" font-size="6" fill="#fff" font-family="Oxygen,sans-serif" transform="rotate(45 24 12)">HOT</text></svg>
  <div class="f-name">Rugs</div><div class="f-no">Item No. : 1254</div>
  <div class="price hot" style="left:82px;top:70px">$190.00</div>
</article>
<article class="abs f-card" style="left:199px">
  <div class="f-img" role="img" aria-label="Red and white patterned cushions on a green rug" style="background:linear-gradient(135deg,#8a2a1c,#c4553a 50%,#6d6d3a)"></div>
  <div class="f-name">Rugs New</div><div class="f-no">Item No. : 1254</div>
  <div class="price" style="left:82px;top:70px">$190.00</div>
</article>
<article class="abs f-card" style="left:353px">
  <div class="f-img" role="img" aria-label="Red and black glass vases with pink flowers" style="background:linear-gradient(135deg,#c9b8c8,#b52030 50%,#2a2a2a)"></div>
  <div class="f-name">Dine</div><div class="f-no">Item No. : 1254</div>
  <div class="price" style="left:82px;top:70px"><s>$230.00</s>$190.00</div>
</article>
<article class="abs f-card" style="left:507px">
  <div class="f-img" role="img" aria-label="Stack of black and white striped towels" style="background:linear-gradient(#d8d4cc,#3a3a3a 60%,#e0e0e0)"></div>
  <div class="f-name">Bathe</div><div class="f-no">Item No. : 1254</div>
  <div class="price" style="left:82px;top:70px">$190.00</div>
</article>

<!-- Latest -->
<h2 class="abs section-title" style="left:44px;top:625px;color:#222">Latest Products</h2>
<svg class="abs wave" style="left:165px;top:631px" width="473" height="6"><line x1="0" y1="3" x2="473" y2="3" stroke="#aaa" stroke-width=".8" stroke-dasharray="2 2"/></svg>

<article class="abs l-card" style="left:45px;top:650px">
  <div class="l-img" role="img" aria-label="Black and white table runner with potted plant" style="background:linear-gradient(#6b3e2a,#2a2a2a 55%,#c8c8c8)"></div>
  <div class="l-name">Rugs New</div><div class="l-no">Item No. : 1254</div>
  <div class="price hot"><s>$230.00</s>$190.00</div>
</article>
<article class="abs l-card" style="left:190px;top:650px">
  <div class="l-img" role="img" aria-label="White armchair with decorative cushion" style="background:linear-gradient(#f0eeea,#cfc8bd)"></div>
  <div class="l-name">Decorative</div><div class="l-no">Item No. : 1254</div>
  <div class="price">$190.00</div>
</article>
<article class="abs l-card" style="left:335px;top:650px">
  <div class="l-img" role="img" aria-label="Cream dining room with round mirror" style="background:linear-gradient(#c9bba4,#ebe4d6)"></div>
  <div class="l-name">Decorative</div><div class="l-no">Item No. : 1254</div>
  <div class="price">$190.00</div>
</article>
<article class="abs l-card" style="left:45px;top:782px">
  <div class="l-img" role="img" aria-label="Round rug with colourful petal border" style="background:radial-gradient(circle,#d8c49a 40%,#e04b6a 60%,#3a2a22 90%)"></div>
  <div class="l-name">Rugs</div><div class="l-no">Item No. : 1254</div>
  <div class="price">$190.00</div>
</article>
<article class="abs l-card" style="left:190px;top:782px">
  <div class="l-img" role="img" aria-label="Dining table with beige tablecloth and cake stand" style="background:linear-gradient(#3a2c22,#c8b08a 60%,#8a6a48)"></div>
  <div class="l-name">Dine</div><div class="l-no">Item No. : 1254</div>
  <div class="price">$190.00</div>
</article>
<article class="abs l-card" style="left:335px;top:782px">
  <div class="l-img" role="img" aria-label="Colourful bead garlands on white decor" style="background:linear-gradient(135deg,#e9e6e2,#d6a6b8 50%,#eee)"></div>
  <div class="l-name">Decorative</div><div class="l-no">Item No. : 1254</div>
  <div class="price"><s>$230.00</s>$190.00</div>
</article>

<aside class="abs offer">
  <div class="offer-img" role="img" aria-label="Folded multicoloured knitted throw"></div>
  <div class="offer-txt">Special<div class="offer-big">OFFER<span>15%</span> <small>off</small></div></div>
</aside>
<aside class="abs womens">
  <div class="womens-photo" role="img" aria-label="Model wearing a pink top"></div>
  <h4>Women's<br>Wear</h4>
  <p>Lorem Ipsum is simply dummy text of the print...</p>
  <a class="buy">Buy It</a>
</aside>

<!-- Why shop -->
<div class="abs why"></div>
<div class="abs why-label">Why Shop With Us?</div>
<div class="abs why-item" style="left:162px"><svg width="14" height="18"><rect x="2" y="8" width="10" height="9" fill="#222"/><path d="M4 8V5a3 3 0 0 1 6 0V8" fill="none" stroke="#222" stroke-width="1.6"/></svg>100% Secure<br>Shopping</div>
<div class="abs why-item" style="left:250px"><svg width="20" height="20"><circle cx="10" cy="10" r="8" fill="none" stroke="#222" stroke-width="1.6"/><path d="M6 10L9 13L14 7" fill="none" stroke="#222" stroke-width="1.6"/></svg>Money Back<br>Guarantee</div>
<div class="abs why-item" style="left:342px"><svg width="38" height="18"><rect x="0" y="3" width="22" height="11" fill="#222"/><path d="M23 6H31L35 10V14H23Z" fill="#222"/><circle cx="7" cy="15" r="2.5" fill="#222" stroke="#fff"/><circle cx="29" cy="15" r="2.5" fill="#222" stroke="#fff"/></svg>FREE Delivery<br>over £300*</div>
<div class="abs why-item" style="left:458px"><svg width="20" height="20"><circle cx="10" cy="10" r="8" fill="none" stroke="#222" stroke-width="1.6"/><path d="M13 6L11 11L7 14L9 9Z" fill="#222"/></svg>Fast<br>Dispatch</div>
<div class="abs why-item" style="left:537px"><svg width="20" height="20"><circle cx="10" cy="10" r="8" fill="none" stroke="#222" stroke-width="1.6"/><path d="M6 10L9 13L16 4" fill="none" stroke="#222" stroke-width="2"/></svg>Great Customer<br>Feedback</div>

<!-- Connect -->
<div class="abs connect"></div>
<div class="abs connect-inner"></div>
<div class="abs connect-label" style="left:62px;top:992px">FOLLOW US!</div>
<div class="abs social" style="left:62px;top:1009px">
  <i style="background:#3b5b98"></i><i style="background:#2aa3d8"></i><i style="background:#c9232c"></i><i style="background:#ef7a22"></i><i style="background:#d63a2b"></i>
</div>
<div class="abs vrule" style="left:167px"></div>
<div class="abs connect-label" style="left:189px;top:992px">CALL US ON</div>
<svg class="abs" style="left:189px;top:1004px" width="18" height="20" viewBox="0 0 18 20"><path d="M4 1L7 5L5 8Q7 12 10 14L13 12L17 15L15 19Q3 17 1 4Z" fill="#222"/></svg>
<div class="abs phone">+123-456-7890</div>
<div class="abs vrule" style="left:333px"></div>
<div class="abs connect-label" style="left:355px;top:992px">NEWSLETTER</div>
<div class="abs news-input">ENTER YOUR EMAIL FOR THE OUR NEWS!</div>
<div class="abs submit">SUBMIT</div>

<!-- Footer -->
<footer class="abs footer"></footer>
<div class="abs foot-col" style="left:62px"><h5>Quick Link</h5>
  <ul style="grid-template-columns:auto auto"><li>Home</li><li>Decorative</li><li>Rugs</li><li>Sleep</li><li>Bathe</li><li>Contact Us</li><li>Dine</li></ul></div>
<div class="abs foot-col" style="left:165px"><h5>Customer Service</h5>
  <ul style="grid-template-columns:auto auto"><li>My Account</li><li>Delivery</li><li>Terms and Conditions</li><li>Customer Service</li><li>Price Promise</li><li>Customer Reviews</li><li>Returns Policy</li><li>Gift Vouchers</li></ul></div>
<div class="abs foot-col" style="left:339px"><h5>Popular Products</h5>
  <ul style="grid-template-columns:auto auto"><li>Lorem ipsum</li><li>Lorem ipsum Sit</li><li>Lorem ipsum Sit</li><li>Lorem ipsum</li><li>Lorem ipsum</li><li>Lorem ipsum Sit</li><li>Lorem ipsum Sit</li><li>Lorem ipsum</li></ul></div>
<div class="abs foot-brand">studio nine harbors</div>
<div class="abs accept">We Accept :</div>
<div class="abs pay" style="left:539px"></div>
<div class="abs pay" style="left:568px"></div>
<div class="abs pay" style="left:597px"></div>
<div class="abs copyright">© 2014 studio nine harbors. All Rights Reserved.</div>

</body>
</html>
```